Professional & attention grabbing.

A business card design, front and back. I already have a logo I will attach, but I am open to something new as well.
Things to include:
Name:
Title:
Phone:
Email:
Wanting something that is professional but attention grabbing.
Also we do a lot of work using drones on natural gas pipelines (leading the future)if you want to include any of that. I'm open to ideas.
Target Market(s)
Natural gas transmission industry / greenhouse gas mitigation industry
Industry/Entity Type
Business
Colors
Designer to choose colors to be used in the design.
Look and feel
Each slider illustrates characteristics of the customer's brand and the style your logo design should communicate.

```html
<!DOCTYPE html>
<html lang="en">
<head>
<meta charset="utf-8">
<title>Kestrel Inspections – Business Card</title>
<link rel="stylesheet" href="https://fonts.googleapis.com/css2?family=Exo+2:wght@400;500;700&display=swap">
<style>
  :root {
    --stage: #000000;
    --brand-red: #c01f25;
    --paper: #fdfdfd;
    --ink: #3a3a3c;
    --ink-soft: #444446;
    --on-red: #ffffff;
  }
  * { margin: 0; padding: 0; box-sizing: border-box; }
  html, body {
    width: 1200px; height: 900px; overflow: hidden;
    background: var(--stage);
    font-family: "Exo 2", Arial, sans-serif;
  }
  .stage { position: relative; width: 1200px; height: 900px; }

  .card {
    position: absolute; top: 271px;
    width: 458px; height: 281px;
    border-radius: 12px; overflow: hidden;
  }

  /* Front */
  .card-front { left: 137px; background: var(--paper); }
  .front-band {
    position: absolute; left: 328px; top: 0;
    width: 130px; height: 100%;
    background: var(--brand-red);
  }
  .front-frame {
    position: absolute; left: 328px; top: 82px;
    width: 101px; height: 118px;
    background: var(--paper);
  }
  .wordmark {
    position: absolute; display: flex; align-items: center; gap: 8px;
    font-weight: 700; letter-spacing: 0.5px; white-space: nowrap;
  }
  .wordmark-square { display: block; flex: none; }
  .front-wordmark { left: 28px; top: 37px; font-size: 21px; color: var(--ink); }
  .front-wordmark .wordmark-square { width: 24px; height: 24px; background: var(--brand-red); }

  .person { position: absolute; left: 28px; top: 120px; }
  .person-name {
    font-size: 20px; font-weight: 700; color: var(--brand-red);
    letter-spacing: 0.3px; line-height: 24px;
  }
  .person-title {
    font-size: 12.5px; font-weight: 500; color: var(--ink);
    letter-spacing: 0.5px; line-height: 14px;
  }

  .contact-list { position: absolute; left: 28px; top: 174px; list-style: none; }
  .contact-item {
    display: flex; align-items: center; gap: 7px;
    font-size: 13px; color: var(--ink-soft); height: 21px;
  }
  .contact-icon { width: 11px; height: 11px; flex: none; }

  .address {
    position: absolute; left: 28px; top: 222px;
    font-style: normal; font-size: 13px; line-height: 17px; color: var(--ink-soft);
  }

  /* Back */
  .card-back { left: 626px; background: var(--brand-red); color: var(--on-red); }
  .back-wordmark {
    left: 50%; top: 112px; transform: translateX(-50%);
    font-size: 30px; color: var(--on-red); gap: 12px;
  }
  .back-wordmark .wordmark-square { width: 38px; height: 38px; background: var(--on-red); }
  .website {
    position: absolute; left: 0; right: 0; top: 226px;
    text-align: center; font-size: 13px; font-weight: 500; letter-spacing: 0.3px;
  }
</style>
</head>
<body>
<main class="stage">

  <section class="card card-front" aria-label="Business card front">
    <div class="front-band"></div>
    <div class="front-frame"></div>

    <div class="wordmark front-wordmark">
      <span class="wordmark-square"></span>
      <span class="wordmark-text">KESTREL INSPECTIONS</span>
    </div>

    <div class="person">
      <p class="person-name">DANA WHITFIELD</p>
      <p class="person-title">DIRECTOR</p>
    </div>

    <ul class="contact-list">
      <li class="contact-item">
        <svg class="contact-icon" viewBox="0 0 11 11" aria-hidden="true">
          <rect width="11" height="11" rx="1.5" fill="#c01f25"/>
          <path d="M3 3.2h5l-.6 1.3H3.6z M3.3 5h4.4v2.8H3.3z" fill="#fff"/>
        </svg>
        <span>555-014-2870</span>
      </li>
      <li class="contact-item">
        <svg class="contact-icon" viewBox="0 0 11 11" aria-hidden="true">
          <rect width="11" height="11" rx="1.5" fill="#c01f25"/>
          <rect x="2.5" y="3.3" width="6" height="4.4" fill="#fff"/>
          <path d="M2.5 3.3l3 2.3 3-2.3" fill="none" stroke="#c01f25" stroke-width="0.8"/>
        </svg>
        <span>hello@kestrelinspect.com</span>
      </li>
    </ul>

    <address class="address">418 Harrow Lane,<br>Millbrook Heights, Ostara</address>
  </section>

  <section class="card card-back" aria-label="Business card back">
    <div class="wordmark back-wordmark">
      <span class="wordmark-square"></span>
      <span class="wordmark-text">KESTREL INSPECTIONS</span>
    </div>
    <p class="website">www.kestrelinspect.com</p>
  </section>

</main>
</body>
</html>
```